HARBORLINE AUTO GLASS

Mobile Glass Shop:

1) Windshield REPAIR 2)Windshield replacment 3) Rear Windshield Replacment 4) Side Window Replacment 5) car window replacment 6) Power Window Repair.

Schedual a service within 24 hour with one of our certified technicians.
Updates

See "brightvane auto repair" web site for referance on the nature of our buisness and service. www.brightvane-example.com

Coding

```html
<!DOCTYPE html>
<html lang="en">
<head>
<meta charset="utf-8">
<title>Harborline Auto Glass</title>
<link href="https://fonts.googleapis.com/css2?family=Roboto:wght@400;500;700&display=swap" rel="stylesheet">
<style>
:root{
  --sky:#2cb0e6;
  --sky-dark:#2795d0;
  --navy:#1f6fb5;
  --ink:#1d1d1d;
  --text:#555;
  --light:#f3f3f3;
  --white:#fff;
  --star:#f5d80b;
}
*{box-sizing:border-box;margin:0;padding:0}
html,body{width:1200px;height:4108px;overflow:hidden}
body{position:relative;font-family:"Roboto",Arial,sans-serif;color:var(--ink);background:var(--white)}
.abs{position:absolute}
.btn{position:absolute;display:flex;align-items:center;justify-content:center;gap:10px;border-radius:30px;background:var(--sky);color:var(--white);font-weight:700;font-size:15px;text-transform:uppercase}
.btn .go{width:14px;height:14px;border-radius:50%;background:var(--white);display:inline-flex;align-items:center;justify-content:center}
.btn .go svg{width:8px;height:8px}
.section-title{position:absolute;left:0;width:1200px;text-align:center;font-size:33px;font-weight:700;text-transform:uppercase}
.section-title::after{content:"";display:block;width:40px;height:3px;background:var(--sky);margin:10px auto 0}

/* top bar */
.topbar{top:0;left:0;width:1200px;height:48px;background:var(--sky);color:var(--white);font-size:15px}
.topbar .item{position:absolute;top:15px;display:flex;align-items:center;gap:8px}
.topbar .social{position:absolute;top:17px;width:12px;height:12px;border-radius:50%;border:2px solid var(--white)}

/* header */
.brand{display:flex;align-items:center;gap:10px;color:var(--navy);font-weight:700;line-height:1.05}
.brand .mark{background:var(--navy);border-radius:4px}
.header .brand{position:absolute;left:115px;top:66px;font-size:18px}
.header .brand .mark{width:40px;height:62px}
.nav a{position:absolute;top:94px;font-size:15px;color:#333;text-decoration:none;text-transform:uppercase}
.nav a.active{color:var(--sky)}
.login{left:959px;top:80px;width:129px;height:45px;background:var(--sky-dark)}

/* hero */
.hero{top:152px;left:0;width:1200px;height:662px;clip-path:polygon(0 0,100% 0,100% 582px,0 662px);
  background:linear-gradient(110deg,#5a6068 0%,#3b3f46 35%,#2c3138 55%,#46536a 80%,#2d5ea8 100%)}
.hero .welcome{left:571px;top:176px;font-size:32px;font-weight:700;color:var(--white)}
.hero h1{position:absolute;left:571px;top:230px;font-size:58px;line-height:68px;font-weight:700;color:var(--white);width:600px}
.hero .btn{left:571px;top:399px;width:171px;height:44px}

/* services */
.card{position:absolute;top:958px;width:233px;height:319px;background:var(--white);box-shadow:0 2px 10px rgba(0,0,0,.12)}
.card .photo{height:152px;background:linear-gradient(135deg,#8d949c,#414852)}
.card h3{position:absolute;left:16px;top:180px;font-size:14px;font-weight:700;text-transform:uppercase;line-height:20px;width:205px}
.card p{position:absolute;left:16px;top:212px;font-size:12px;line-height:20px;color:#333;width:205px}
.card.tall h3{top:170px}
.card.tall p{top:218px}
.card .btn{left:16px;top:271px;width:131px;height:29px;font-size:12px;background:var(--navy)}
.card.active{border-bottom:3px solid var(--sky)}

/* about */
.about{top:1452px;left:0;width:1200px;height:666px;background:var(--light);clip-path:polygon(0 64px,100% 0,100% 100%,0 100%)}
.about h2{position:absolute;left:108px;top:145px;font-size:32px;font-weight:700}
.about h2::after{content:"";display:block;width:40px;height:3px;background:var(--sky);margin-top:4px}
.about p{position:absolute;left:108px;top:208px;width:451px;font-size:15px;line-height:25.7px;color:#333;text-align:justify}
.about .btn{left:108px;top:514px;width:171px;height:45px}
.about .ring{left:635px;top:123px;width:456px;height:456px;border-radius:50%;border:4px solid var(--sky);border-right-color:transparent;border-bottom-color:transparent;transform:rotate(-10deg)}
.about .photo{left:638px;top:126px;width:450px;height:450px;border-radius:50%;background:radial-gradient(circle at 55% 45%,#7c8a7a,#3e4448 70%)}

/* schedule */
.schedule{top:2118px;left:0;width:1200px;height:313px;background:linear-gradient(90deg,#2aa6de,#2f9bd8)}
.schedule h2{position:absolute;left:0;width:1200px;top:60px;text-align:center;color:var(--white);font-size:32px;font-weight:700}
.schedule h2::after{content:"";display:block;width:40px;height:3px;background:var(--white);margin:12px auto 0}
.schedule p{position:absolute;left:150px;width:900px;top:132px;text-align:center;color:var(--white);font-size:15px;line-height:26px}
.schedule .btn{left:514px;top:206px;width:172px;height:43px;background:var(--navy)}

/* why choose */
.why{position:absolute;top:2594px;width:270px;height:427px;border-radius:135px;background:var(--white);box-shadow:0 6px 22px rgba(0,0,0,.1);text-align:center}
.why svg.icon{position:absolute;left:85px;top:40px;width:100px;height:80px}
.why h3{position:absolute;left:0;width:100%;top:140px;font-size:22px;font-weight:700}
.why p{position:absolute;left:25px;width:220px;top:205px;font-size:14px;line-height:22.5px;color:var(--text)}
.why .more{position:absolute;left:112px;top:345px;width:46px;height:46px;border-radius:50%;background:var(--sky);display:flex;align-items:center;justify-content:center}
.why .more.dark{background:var(--navy)}

/* testimonials */
.testimonials{top:3109px;left:0;width:1200px;height:602px;background:linear-gradient(120deg,#2c7ec4,#2f8ed0 60%,#2b7bc0);clip-path:polygon(0 0,100% 0,100% 538px,0 602px)}
.testimonials h2{position:absolute;left:0;width:1200px;top:86px;text-align:center;color:var(--white);font-size:32px;font-weight:700}
.testimonials h2::after{content:"";display:block;width:40px;height:3px;background:var(--white);margin:10px auto 0}
.testimonials p{position:absolute;left:188px;width:824px;top:170px;text-align:justify;text-align-last:center;color:var(--white);font-size:15px;line-height:27.5px}
.avatar{position:absolute;border-radius:50%;background:radial-gradient(circle,#9fb6cc,#3c6590)}
.testimonials .name{position:absolute;left:0;width:1200px;top:444px;text-align:center;color:var(--white);font-size:16px;font-weight:700}
.testimonials .stars{position:absolute;left:555px;top:474px;display:flex;gap:4px}

/* footer */
.footer .brand{position:absolute;left:112px;top:3822px;font-size:24px}
.footer .brand .mark{width:56px;height:84px}
.fsocial{position:absolute;top:3946px;width:30px;height:30px;border-radius:50%;background:#e8e8e8}
.fcol h4{position:absolute;top:3787px;font-size:16px;font-weight:700;text-transform:uppercase}
.fcol a{position:absolute;font-size:15px;color:#555;text-decoration:none;display:flex;align-items:center;gap:12px}
.fcol a::before{content:"»";color:var(--sky);font-size:14px}
.contact-row{position:absolute;left:863px;font-size:15px;color:#555;line-height:22px}
.contact-row b{display:block;font-size:12px;color:#333}
.contact-row svg{position:absolute;left:0;top:3px;width:13px;height:13px}
.contact-row div{padding-left:26px}
.divider{position:absolute;left:112px;top:4038px;width:976px;height:1px;background:#ddd}
.copy{position:absolute;left:0;width:1200px;top:4066px;text-align:center;font-size:15px;color:#555}
.totop{position:absolute;left:1123px;top:4018px;width:34px;height:34px;border-radius:50%;background:var(--sky);display:flex;align-items:center;justify-content:center}
</style>
</head>
<body>

<div class="abs topbar">
  <div class="item" style="left:112px">
    <svg width="13" height="13" viewBox="0 0 24 24"><rect width="24" height="24" rx="4" fill="#fff"/><path d="M7 5l3 3-2 2c1 2 3 4 5 5l2-2 3 3-2 3c-6 0-11-5-11-11z" fill="#2cb0e6"/></svg>
    +1 555 014 2290
  </div>
  <div class="item" style="left:283px">
    <svg width="15" height="11" viewBox="0 0 24 18"><rect x="1" y="1" width="22" height="16" rx="2" fill="none" stroke="#fff" stroke-width="2"/><path d="M1 2l11 8 11-8" fill="none" stroke="#fff" stroke-width="2"/></svg>
    info@harborlineautoglass.com
  </div>
  <span class="social" style="left:963px" aria-label="Social profile"></span>
  <span class="social" style="left:1000px" aria-label="Social profile"></span>
  <span class="social" style="left:1037px" aria-label="Social profile"></span>
  <span class="social" style="left:1074px" aria-label="Social profile"></span>
</div>

<header class="header">
  <div class="brand"><span class="mark"></span><span>HARBORLINE<br>AUTO GLASS</span></div>
  <nav class="nav">
    <a class="active" style="left:424px">Home</a>
    <a style="left:498px">About Us</a>
    <a style="left:600px">Services</a>
    <a style="left:700px">Testimonials</a>
    <a style="left:838px">Contact Us</a>
  </nav>
  <div class="btn login">Login
    <svg width="11" height="13" viewBox="0 0 12 14"><rect x="1" y="6" width="10" height="8" rx="1" fill="#fff"/><path d="M3 6V4a3 3 0 016 0v2" fill="none" stroke="#fff" stroke-width="2"/></svg>
  </div>
</header>

<section class="abs hero" role="img" aria-label="Two smiling technicians in blue overalls fitting a windshield onto a car in a workshop">
  <div class="abs welcome">WELCOME TO</div>
  <h1>HARBORLINE AUTO GLASS</h1>
  <div class="btn">Get Started <span class="go"><svg viewBox="0 0 8 8"><path d="M2 1l4 3-4 3" fill="none" stroke="#2cb0e6" stroke-width="2"/></svg></span></div>
</section>

<h2 class="section-title" style="top:880px">Our Services</h2>

<div class="card" style="left:115px">
  <div class="photo" role="img" aria-label="Technician repairing a windshield"></div>
  <h3>Windshield Repair</h3>
  <p>Lorem ipsum dolor sitconsectetur adipiscing elitedsed do eiusmod</p>
  <div class="btn">Read More <span class="go"><svg viewBox="0 0 8 8"><path d="M2 1l4 3-4 3" fill="none" stroke="#1f6fb5" stroke-width="2"/></svg></span></div>
</div>
<div class="card" style="left:361px">
  <div class="photo" role="img" aria-label="Close-up of tools working on car glass"></div>
  <h3>Power Window Repair</h3>
  <p>Lorem ipsum dolor sitconsectetur adipiscing elitedsed do eiusmod</p>
  <div class="btn">Read More <span class="go"><svg viewBox="0 0 8 8"><path d="M2 1l4 3-4 3" fill="none" stroke="#1f6fb5" stroke-width="2"/></svg></span></div>
</div>
<div class="card tall active" style="left:606px">
  <div class="photo" role="img" aria-label="Two technicians replacing a rear windshield" style="background:linear-gradient(135deg,#6d9ccc,#2f4f7a)"></div>
  <h3>Rear Windshield Replacment</h3>
  <p>Lorem ipsum dolor sitconsectetur adipiscing elitedsed do eiusmod</p>
  <div class="btn" style="top:268px">Read More <span class="go"><svg viewBox="0 0 8 8"><path d="M2 1l4 3-4 3" fill="none" stroke="#1f6fb5" stroke-width="2"/></svg></span></div>
</div>
<div class="card" style="left:852px">
  <div class="photo" role="img" aria-label="Technician lifting a car window pane with suction cups" style="background:linear-gradient(135deg,#c9ced3,#5b6168)"></div>
  <h3>Car Window Replacment</h3>
  <p>Lorem ipsum dolor sitconsectetur adipiscing elitedsed do eiusmod</p>
  <div class="btn">Read More <span class="go"><svg viewBox="0 0 8 8"><path d="M2 1l4 3-4 3" fill="none" stroke="#1f6fb5" stroke-width="2"/></svg></span></div>
</div>

<div class="btn" style="left:514px;top:1329px;width:172px;height:45px">View More <span class="go"><svg viewBox="0 0 8 8"><path d="M2 1l4 3-4 3" fill="none" stroke="#2cb0e6" stroke-width="2"/></svg></span></div>

<section class="abs about">
  <h2>ABOUT US</h2>
  <p>Lorem ipsum dolor sit amet, consectetur adipiscing elit, sed do eiusmod tempor incididunt ut labore et dolore magna aliqua. Ut enim ad minim veniam, quis nostrud exercitation ullamco laboris nisi ut aliquip ex ea commodo consequat. Duis aute irure dolor in reprehenderit in voluptate velit esse cillum dolore eu fugiat nulla pariatur. Excepteur sint occaecat cupidatat non proident, sunt in culpa qui officia deserunt mollit anim id est laborumLorem ipsum dolor sit amet, consectetur adipiscing elit, sed do eiusmod tempor incididunt ut labore et dolore magna aliqua. Ut enim ad minim veniam, quis nostrud exercitation ullamco laboris nisi ut aliquip ex ea commodo consequats aute irure dolor &nbsp;reprehenderit.</p>
  <div class="btn">Learn More <span class="go"><svg viewBox="0 0 8 8"><path d="M2 1l4 3-4 3" fill="none" stroke="#2cb0e6" stroke-width="2"/></svg></span></div>
  <div class="abs ring"></div>
  <div class="abs photo" role="img" aria-label="Technician in green overalls installing a car side window"></div>
</section>

<section class="abs schedule" role="img" aria-label="Blue tinted band over a workshop scene">
  <h2>SCHEDULE A SERVICE WITHIN 24 HOUR</h2>
  <p>Lorem ipsum dolor sit amet, consectetur adipiscing elit, sed do eiusmod tempor incididunt ut labore et dolore magna aliqua.<br>Ut enim ad minim veniam, quis nostrud exercitation ullamco laboris nisi ut aliquip ex ea commodo consequat.</p>
  <div class="btn">Get A Quote <span class="go"><svg viewBox="0 0 8 8"><path d="M2 1l4 3-4 3" fill="none" stroke="#1f6fb5" stroke-width="2"/></svg></span></div>
</section>

<h2 class="section-title" style="top:2512px">Why Choose Us</h2>

<div class="why" style="left:134px">
  <svg class="icon" viewBox="0 0 100 80"><path d="M12 48l8-18h40l8 18z" fill="none" stroke="#2795d0" stroke-width="5"/><rect x="8" y="46" width="66" height="18" rx="4" fill="#2795d0"/><circle cx="22" cy="56" r="4" fill="#fff"/><circle cx="60" cy="56" r="4" fill="#fff"/><rect x="14" y="62" width="10" height="10" fill="#2795d0"/><rect x="58" y="62" width="10" height="10" fill="#2795d0"/><circle cx="74" cy="22" r="14" fill="none" stroke="#2cb0e6" stroke-width="5"/><path d="M74 36v38" stroke="#2cb0e6" stroke-width="6"/></svg>
  <h3>Lorem ipsumed</h3>
  <p>Lorem ipsum dolor sited ametes consectetur adipiscing elites sed do eiusmod tempor incididunt ute exercitation ullamco laboris nisie commodo consequated.</p>
  <div class="more"><svg width="14" height="14" viewBox="0 0 14 14"><circle cx="7" cy="7" r="7" fill="#fff"/><path d="M5 4l3 3-3 3" fill="none" stroke="#2cb0e6" stroke-width="2"/></svg></div>
</div>
<div class="why" style="left:464px">
  <svg class="icon" viewBox="0 0 100 80"><circle cx="82" cy="14" r="12" fill="#2795d0"/><rect x="80" y="7" width="4" height="10" fill="#fff"/><rect x="80" y="19" width="4" height="4" fill="#fff"/><path d="M30 40l6-12h26l6 12z" fill="none" stroke="#2cb0e6" stroke-width="4"/><rect x="22" y="40" width="56" height="20" rx="4" fill="none" stroke="#2795d0" stroke-width="4"/><rect x="30" y="46" width="10" height="6" fill="#2795d0"/><rect x="60" y="46" width="10" height="6" fill="#2795d0"/><rect x="26" y="60" width="10" height="10" fill="#2795d0"/><rect x="64" y="60" width="10" height="10" fill="#2795d0"/><rect x="10" y="72" width="80" height="4" fill="#2795d0"/></svg>
  <h3>Lorem ipsumed</h3>
  <p>Lorem ipsum dolor sited ametes consectetur adipiscing elites sed do eiusmod tempor incididunt ute exercitation ullamco laboris nisie commodo consequated.</p>
  <div class="more dark"><svg width="14" height="14" viewBox="0 0 14 14"><circle cx="7" cy="7" r="7" fill="#fff"/><path d="M5 4l3 3-3 3" fill="none" stroke="#1f6fb5" stroke-width="2"/></svg></div>
</div>
<div class="why" style="left:796px">
  <svg class="icon" viewBox="0 0 100 80"><rect x="44" y="4" width="12" height="8" rx="2" fill="#2795d0"/><path d="M6 16h88l-6 28H12z" fill="none" stroke="#2795d0" stroke-width="5"/><path d="M16 24h68l-4 12H20z" fill="#2cb0e6"/><path d="M22 32l14-6" stroke="#fff" stroke-width="3"/><rect x="14" y="52" width="72" height="5" rx="2" fill="#2795d0"/></svg>
  <h3 style="top:130px">Lorem ipsumed</h3>
  <p style="top:195px">Lorem ipsum dolor sited ametes consectetur adipiscing elites sed do eiusmod tempor incididunt ute exercitation ullamco laboris nisie commodo consequated.</p>
  <div class="more" style="top:338px"><svg width="14" height="14" viewBox="0 0 14 14"><circle cx="7" cy="7" r="7" fill="#fff"/><path d="M5 4l3 3-3 3" fill="none" stroke="#2cb0e6" stroke-width="2"/></svg></div>
</div>

<section class="abs testimonials" role="img" aria-label="Blue tinted band over a technician at work">
  <h2>OUR TESTIMONIALS</h2>
  <p>Lorem ipsum dolor sit amet, consectetur adipiscing elit, sed do eiusmod tempor incididunt ut labore et dolore magna aliqua. Ut enim ad minim veniam, quis nostrud exercitation ullamco laboris nisi ut aliquip ex ea commodo consequat. Duis aute irure dolor in reprehenderit in voluptate velit esse cillum dolore eu fugiat nulla pariatur. Lorem ipsum dolor sit amet, consectetur adipiscing elit, sed do eiusmod tempor incididunt ut labore et dolore magna aliqua. Ut enim ad minim veniam, quis nostrud exercitation ullamco laboris nisi aliquip commodo &nbsp;irure dolor reprehenderited.</p>
  <div class="avatar" style="left:465px;top:351px;width:70px;height:70px;opacity:.7" role="img" aria-label="Client portrait"></div>
  <div class="avatar" style="left:662px;top:351px;width:70px;height:70px;opacity:.7" role="img" aria-label="Client portrait"></div>
  <div class="avatar" style="left:552px;top:338px;width:96px;height:96px;border:3px solid #fff;background:radial-gradient(circle,#c7d3de,#4a6a8a)" role="img" aria-label="Portrait of the featured client"></div>
  <div class="name">Daniel Rourke</div>
  <div class="stars">
    <svg width="15" height="15" viewBox="0 0 24 24"><path d="M12 1l3.4 7 7.6 1-5.5 5.3 1.3 7.7L12 18.3 5.2 22l1.3-7.7L1 9l7.6-1z" fill="#f5d80b"/></svg>
    <svg width="15" height="15" viewBox="0 0 24 24"><path d="M12 1l3.4 7 7.6 1-5.5 5.3 1.3 7.7L12 18.3 5.2 22l1.3-7.7L1 9l7.6-1z" fill="#f5d80b"/></svg>
    <svg width="15" height="15" viewBox="0 0 24 24"><path d="M12 1l3.4 7 7.6 1-5.5 5.3 1.3 7.7L12 18.3 5.2 22l1.3-7.7L1 9l7.6-1z" fill="#f5d80b"/></svg>
    <svg width="15" height="15" viewBox="0 0 24 24"><path d="M12 1l3.4 7 7.6 1-5.5 5.3 1.3 7.7L12 18.3 5.2 22l1.3-7.7L1 9l7.6-1z" fill="#f5d80b"/></svg>
    <svg width="15" height="15" viewBox="0 0 24 24"><path d="M12 1l3.4 7 7.6 1-5.5 5.3 1.3 7.7L12 18.3 5.2 22l1.3-7.7L1 9l7.6-1z" fill="#f5d80b"/></svg>
  </div>
</section>

<footer class="footer">
  <div class="brand"><span class="mark"></span><span>HARBORLINE<br>AUTO GLASS</span></div>
  <span class="fsocial" style="left:140px" aria-label="Social profile"></span>
  <span class="fsocial" style="left:178px" aria-label="Social profile"></span>
  <span class="fsocial" style="left:216px" aria-label="Social profile"></span>
  <span class="fsocial" style="left:255px" aria-label="Social profile"></span>

  <div class="fcol">
    <h4 style="left:410px">Quick Links</h4>
    <a style="left:410px;top:3828px">Home</a>
    <a style="left:410px;top:3862px">About Us</a>
    <a style="left:410px;top:3896px">Service</a>
    <a style="left:410px;top:3931px">Testimonials</a>
    <a style="left:410px;top:3965px">Contact Us</a>
  </div>
  <div class="fcol">
    <h4 style="left:629px">Other Links</h4>
    <a style="left:629px;top:3828px">Legal Information</a>
    <a style="left:629px;top:3862px">Terms &amp; Condition</a>
    <a style="left:629px;top:3896px">Privacy Policy</a>
    <a style="left:629px;top:3931px">Support</a>
    <a style="left:629px;top:3965px">Site Map</a>
  </div>
  <div class="fcol">
    <h4 style="left:863px">Contact Us</h4>
  </div>
  <div class="contact-row" style="top:3826px">
    <svg viewBox="0 0 24 24"><path d="M6 2l4 5-2 3c1 3 3 5 6 6l3-2 5 4-3 4C10 22 2 14 2 5z" fill="#2795d0"/></svg>
    <div><b>Phone</b>+1 555 014 2290</div>
  </div>
  <div class="contact-row" style="top:3878px">
    <svg viewBox="0 0 24 18"><rect width="24" height="18" rx="2" fill="#2795d0"/><path d="M1 2l11 8 11-8" fill="none" stroke="#fff" stroke-width="2"/></svg>
    <div><b>Email</b>info@harborlineautoglass.com</div>
  </div>
  <div class="contact-row" style="top:3932px">
    <svg viewBox="0 0 24 24"><path d="M12 1a8 8 0 018 8c0 6-8 14-8 14S4 15 4 9a8 8 0 018-8z" fill="#2795d0"/><circle cx="12" cy="9" r="3" fill="#fff"/></svg>
    <div><b>Location</b>77 Lorem ipsum dolor itmet<br>consectetur adipiscing elited,</div>
  </div>

  <div class="totop"><svg width="14" height="10" viewBox="0 0 14 10"><path d="M2 8l5-5 5 5" fill="none" stroke="#fff" stroke-width="2.5"/></svg></div>
  <div class="divider"></div>
  <div class="copy">2022 Copyright - &nbsp;Harborline Auto Glass | &nbsp;All Rights Reserved</div>
</footer>

</body>
</html>
```